** Wanted ** Wordpress web design for scaffolding rental and construction company

We need a website design and must be functional to show a basic overview of what our company offers as a service. We have a domain name and a logo but we need web design. This web site should have another scaffolding rental page for construction and renovation as well as a quote section where customers can enter their personal information and also upload photos. The site% 26quot; www.brindlework.com% 26quot; should be intuitive, clear and classy ... The logo must be found on the site in several ways.

Target Market(s)

Professional and no professional

Coding

Coded - Design and coding required

Number of Pages Required

3 page

Font styles to use
Serif
Sans Serif
Decorative
Script

Requirements
Must have
• Our logo
Nice to have
• Slogan:% 26quot; The height% 26 # 224; port% 26 # 233; e hand% 26quot;

```html
<!DOCTYPE html>
<html lang="en">
<head>
<meta charset="utf-8">
<title>Brindlework – Scaffolding &amp; Construction</title>
<link href="https://fonts.googleapis.com/css2?family=Poppins:wght@300;400;500;600;700;800;900&display=swap" rel="stylesheet">
<style>
:root{
  --orange:#f0861e;
  --orange-deep:#e8780f;
  --peach:#fde3cc;
  --ink:#1c1c1c;
  --text:#555555;
  --muted:#8a8a8a;
  --dark:#1f2329;
  --white:#ffffff;
  --line:#e2e2e2;
}
*{margin:0;padding:0;box-sizing:border-box}
html,body{width:1200px;height:4000px;overflow:hidden;background:var(--white)}
body{position:relative;font-family:'Poppins',sans-serif;color:var(--text)}
.abs{position:absolute}
.btn{position:absolute;display:flex;align-items:center;justify-content:center;border:2px solid var(--orange);color:var(--orange);font-weight:500;text-transform:uppercase;background:transparent}

/* hero */
.hero{position:absolute;left:0;top:0;width:1200px;height:700px;overflow:hidden}
.hero-photo{position:absolute;inset:0;background:linear-gradient(120deg,#3b3a37 0%,#2a2824 40%,#4a4337 70%,#2e2b27 100%)}
.hero-diamond{position:absolute;left:-40px;top:150px;width:300px;height:300px;transform:rotate(45deg);background:rgba(240,134,30,.12)}
.brand{position:absolute;display:flex;align-items:center;gap:10px;color:var(--orange);font-weight:700;letter-spacing:1px}
.brand .mark{width:14px;height:14px;background:var(--orange)}
.nav{position:absolute;left:427px;top:40px;display:flex;gap:26px;font-size:14px;color:#e9e9e9;text-transform:uppercase}
.nav .active{color:var(--orange)}
.hero-title{position:absolute;left:127px;top:228px;font-weight:800;font-size:78px;line-height:70px;color:var(--white);letter-spacing:1px}
.hero-title .accent{color:transparent;-webkit-text-stroke:2px var(--orange)}
.slider-dots{position:absolute;left:1153px;top:260px;display:flex;flex-direction:column;gap:15px}
.slider-dots span{width:11px;height:11px;background:#b3aaa0}
.slider-dots .on{background:transparent;border:2px solid var(--orange);transform:rotate(45deg)}

/* headings */
.sec-head{position:absolute;left:0;width:1200px;text-align:center}
.sec-head h2{font-weight:600;font-size:42px;line-height:46px;color:var(--orange);text-transform:uppercase}
.sec-head h2 .dark{color:var(--ink)}
.sec-head p{font-size:15px;color:var(--text);margin-top:10px}

/* services */
.card{position:absolute;top:905px;width:292px;background:var(--white);box-shadow:0 4px 14px rgba(0,0,0,.08);text-align:center}
.card .photo{height:217px;border-bottom-left-radius:40px 30px;border-bottom-right-radius:40px 30px;border-bottom:8px solid var(--peach)}
.card h3{font-weight:500;font-size:18px;color:var(--ink);margin-top:36px}
.card p{font-size:14px;line-height:25px;color:var(--text);padding:0 18px;margin-top:12px}
.card .btn{position:relative;margin:24px auto 28px;width:148px;height:48px;font-size:16px;color:var(--ink)}
.card.featured .photo{border-bottom-color:var(--orange)}
.card .badge{position:absolute;left:118px;top:180px;width:56px;height:56px;transform:rotate(45deg);background:var(--ink);border:3px solid var(--orange)}

/* about */
.welcome-kicker{position:absolute;left:160px;top:1496px;font-size:21px;font-weight:500;color:var(--orange)}
.welcome-title{position:absolute;left:160px;top:1522px;font-size:42px;font-weight:600;color:var(--ink)}
.welcome-text{position:absolute;left:165px;width:400px;font-size:14.5px;line-height:27px;color:var(--text)}
.deco-diamond{position:absolute;transform:rotate(45deg)}

/* gallery */
.gallery-title{position:absolute;left:0;top:2052px;width:1200px;text-align:center;font-size:42px;font-weight:600;color:var(--white)}
.gallery-title .dark{color:var(--ink)}
.gallery-sub{position:absolute;left:0;top:2113px;width:1200px;text-align:center;font-size:15px;color:var(--ink)}
.shot{position:absolute;top:2182px;height:290px;border-radius:14px}
.circle-arrow{position:absolute;top:2300px;width:56px;height:56px;border-radius:50%;background:var(--ink);border:3px solid var(--orange);display:flex;align-items:center;justify-content:center}

/* testimonials */
.quote{position:absolute;left:280px;top:2918px;width:640px;text-align:center;font-size:15.5px;line-height:27px;color:var(--text)}
.client{position:absolute;left:0;top:3022px;width:1200px;text-align:center;font-size:20px;font-weight:500;color:var(--orange)}
.pager{position:absolute;left:560px;top:3076px;display:flex;gap:7px}
.pager span{width:14px;height:14px;border-radius:50%;border:1.5px solid #444}
.pager .on{border-color:var(--orange)}

/* contact */
.discuss{position:absolute;left:174px;top:3225px;font-size:27px;line-height:34px;font-weight:500;color:var(--ink);text-transform:uppercase}
.discuss-sub{position:absolute;left:178px;top:3305px;font-size:16px;color:var(--text)}
.big-phone{position:absolute;left:178px;top:3340px;display:flex;align-items:center;gap:12px;font-size:31px;font-weight:500;color:var(--orange)}
.quote-card{position:absolute;left:644px;top:3176px;width:376px;height:520px;background:var(--white);box-shadow:0 6px 20px rgba(0,0,0,.12);border-radius:6px;text-align:center;z-index:3}
.quote-card h3{font-size:30px;font-weight:600;color:var(--ink);margin-top:50px}
.quote-card h3 span{color:var(--orange)}
.quote-card p{font-size:15px;line-height:25px;color:var(--text);margin-top:8px}
.field{position:absolute;left:40px;width:296px;height:46px;border:1px solid var(--line);border-radius:4px;font-size:12px;color:var(--muted);text-align:left;padding:15px 16px}
.field.focus{border-color:var(--orange);color:var(--orange)}

/* footer */
.footer-bg{position:absolute;left:0;top:3500px;width:1200px;height:438px}
.footer-col h4{position:absolute;top:3764px;font-size:18px;font-weight:600;color:var(--white);text-transform:uppercase}
.footer-col h4 span{color:var(--orange)}
.f-item{position:absolute;font-size:14.5px;color:#d6d6d6;line-height:22px}
.bullet{position:absolute;width:6px;height:6px;border-radius:50%;background:var(--orange)}
.social{position:absolute;top:3818px;width:42px;height:42px;transform:rotate(45deg);background:var(--orange)}
.copyright{position:absolute;left:0;top:3938px;width:1200px;height:62px;background:var(--orange);color:var(--white);font-size:14px;display:flex;align-items:center;justify-content:center}
</style>
</head>
<body>

<!-- HERO -->
<section class="hero">
  <div class="hero-photo" role="img" aria-label="Construction worker in a hard hat building on a site at dusk"></div>
  <div class="hero-diamond"></div>
  <svg class="abs" style="left:0;top:500px" width="1200" height="200" viewBox="0 0 1200 200" preserveAspectRatio="none">
    <path d="M0 75 C40 150 120 165 260 160 C420 155 520 120 650 140 C820 168 1000 215 1120 120 C1160 90 1190 60 1200 20 L1200 200 L0 200 Z" fill="var(--orange)"/>
    <path d="M0 75 C40 150 120 165 260 160 C420 155 520 120 650 140 C820 168 1000 215 1120 120 C1160 90 1190 60 1200 20 L1200 200 L0 200 Z" fill="#fff" transform="translate(0,28)"/>
  </svg>
</section>
<div class="brand" style="left:78px;top:58px;font-size:22px"><span class="mark"></span>BRINDLEWORK</div>
<nav class="nav">
  <span class="active">Home</span><span>About</span><span>Services</span><span>Testimonials</span><span>Gallery</span><span>Contact</span>
</nav>
<div class="btn" style="left:975px;top:28px;width:148px;height:47px;font-size:16px">Get a Quote</div>
<h1 class="hero-title">The<br>Height;<br><span class="accent">Port</span></h1>
<div class="btn" style="left:132px;top:469px;width:168px;height:53px;font-size:18px">Contact Us</div>
<div class="slider-dots"><span></span><span></span><span></span><span class="on"></span><span></span></div>

<!-- SERVICES -->
<header class="sec-head" style="top:750px">
  <h2>Services<br><span class="dark">We Provide You</span></h2>
  <p>Lorem Ipsum is simply dummy text of the printing &amp; type.</p>
</header>

<article class="card" style="left:137px">
  <div class="photo" role="img" aria-label="Building under construction wrapped in scaffolding with a crane" style="background:linear-gradient(160deg,#7fb3d8,#8a7a62 70%,#5b4b3a)"></div>
  <h3>SCAFFOLDING</h3>
  <p>Lorem Ipsum is simply dummy text of the printing and typesetting industry Lorem Ipsum.</p>
  <div class="btn">Learn More</div>
</article>
<article class="card featured" style="left:453px">
  <div class="photo" role="img" aria-label="Wooden house frame under construction with scaffolding" style="background:linear-gradient(160deg,#a9c4dc,#9a7a5d 60%,#6b5240)"></div>
  <div class="badge"></div>
  <h3 style="margin-top:68px">ELEVATION</h3>
  <p>Lorem Ipsum is simply dummy text of the printing and typesetting industry Lorem Ipsum.</p>
  <div class="btn">Learn More</div>
</article>
<article class="card" style="left:770px">
  <div class="photo" role="img" aria-label="Tradesman fitting a wall panel in a bright room" style="background:linear-gradient(160deg,#dcd6cc,#c4a27a 60%,#8e6b47)"></div>
  <h3>RENOVATION</h3>
  <p>Lorem Ipsum is simply dummy text of the printing and typesetting industry Lorem Ipsum.</p>
  <div class="btn">Learn More</div>
</article>

<!-- WELCOME -->
<div class="welcome-kicker">WELCOME TO</div>
<h2 class="welcome-title">BRINDLEWORK</h2>
<p class="welcome-text" style="top:1596px">Lorem Ipsum is simply dummy text of the printing is and typesetting industry. Lorem Ipsum has been the industry's standard dummy text ever since.</p>
<p class="welcome-text" style="top:1694px">Lorem Ipsum is simply dummy text of the printing the and typesetting industry. Lorem Ipsum has been isal industry's standard dummy text ever since the 1500s, when an unknown printer took a galley.</p>
<div class="btn" style="left:168px;top:1822px;width:168px;height:53px;font-size:18px">Learn More</div>
<div class="deco-diamond" style="left:896px;top:1537px;width:90px;height:90px;background:var(--peach)"></div>
<div class="deco-diamond" style="left:686px;top:1822px;width:75px;height:75px;background:var(--peach)"></div>
<div class="deco-diamond" style="left:750px;top:1788px;width:20px;height:20px;background:var(--orange)"></div>
<div class="abs" role="img" aria-label="Model house on blueprints beside a yellow hard hat and tools" style="left:606px;top:1570px;width:515px;height:220px;border-radius:50% 50% 12px 12px / 30% 30% 12px 12px;background:linear-gradient(180deg,#c98b4d 0%,#e9d08a 45%,#cfcfcf 80%,#f2b81d 100%)"></div>

<!-- GALLERY -->
<svg class="abs" style="left:0;top:1950px" width="1200" height="635" viewBox="0 0 1200 635" preserveAspectRatio="none" role="img" aria-label="Orange band with faint photo of construction workers in hard hats">
  <path d="M0 55 C120 10 260 20 420 40 C600 65 720 45 860 20 C1000 -5 1120 15 1200 50 L1200 520 C1130 590 1000 600 850 560 C700 520 520 520 360 560 C220 595 80 610 0 560 Z" fill="var(--orange)"/>
</svg>
<h2 class="gallery-title">WORK <span class="dark">GALLERY</span></h2>
<p class="gallery-sub">Lorem Ipsum is simply dummy text of the printing &amp; type.</p>
<div class="shot" role="img" aria-label="Modern kitchen with dark cabinets" style="left:-20px;width:276px;background:linear-gradient(160deg,#d9cbb6,#6e5a48 60%,#3a2f28)"></div>
<div class="shot" role="img" aria-label="Empty finished living room with grey carpet" style="left:402px;width:396px;background:linear-gradient(180deg,#f1f1ef,#c9c6c1 55%,#8d8a86)"></div>
<div class="shot" role="img" aria-label="Hand holding a tablet showing a kitchen plan" style="left:941px;width:280px;background:linear-gradient(160deg,#efe7da,#c6a57c 55%,#4a4a4a)"></div>
<div class="circle-arrow" style="left:373px">
  <svg width="24" height="16" viewBox="0 0 24 16"><path d="M22 8H3M9 2L3 8l6 6" stroke="#fff" stroke-width="2" fill="none"/></svg>
</div>
<div class="circle-arrow" style="left:769px">
  <svg width="24" height="16" viewBox="0 0 24 16"><path d="M2 8h19M15 2l6 6-6 6" stroke="#fff" stroke-width="2" fill="none"/></svg>
</div>

<!-- TESTIMONIALS -->
<header class="sec-head" style="top:2614px">
  <h2>Testimonials</h2>
  <p style="color:var(--ink);margin-top:6px">What Our Client Say About Us</p>
</header>
<div class="abs" style="left:522px;top:2741px;width:156px;height:156px;border-radius:50%;background:var(--ink);padding:7px">
  <div role="img" aria-label="Client portrait, engineer in a hard hat" style="width:100%;height:100%;border-radius:50%;border:3px solid var(--orange);background:linear-gradient(180deg,#8fc3e8,#4d7fa8)"></div>
</div>
<div class="abs" style="left:640px;top:2740px;width:36px;height:36px;border-radius:50%;background:var(--orange);color:#fff;font-size:26px;font-weight:700;text-align:center;line-height:44px">"</div>
<svg class="abs" style="left:442px;top:2815px" width="36" height="10"><path d="M35 5H2M6 1L2 5l4 4" stroke="#c9c9c9" stroke-width="1.3" fill="none"/></svg>
<svg class="abs" style="left:716px;top:2815px" width="36" height="10"><path d="M1 5h33M30 1l4 4-4 4" stroke="#c9c9c9" stroke-width="1.3" fill="none"/></svg>
<p class="quote">" Lorem Ipsum is simply dummy text of the printing is and typesetting industry. Lorem Ipsum has been the industry's standard dummy text ever since Lorem Ipsum is simply dummy text of the printing "</p>
<div class="client">— Client Name</div>
<div class="pager"><span></span><span class="on"></span><span></span><span></span></div>

<!-- CONTACT + FOOTER -->
<svg class="footer-bg" viewBox="0 0 1200 438" preserveAspectRatio="none">
  <path d="M0 35 C200 10 380 0 560 25 C760 50 1000 40 1200 0 L1200 438 L0 438 Z" fill="var(--dark)"/>
</svg>

<div class="discuss">Discuss Your<br>Projects With Us</div>
<div class="discuss-sub">Lorem Ipsum is simply dummy text of the print !</div>
<div class="big-phone">
  <svg width="36" height="36" viewBox="0 0 36 36"><circle cx="18" cy="18" r="16" fill="none" stroke="var(--orange)" stroke-width="2"/><path d="M13 10l4 4-2 3c1 3 3 5 6 6l3-2 4 4-3 3c-7 0-15-8-15-15z" fill="var(--orange)"/></svg>
  123 456 7890
</div>
<div class="abs" role="img" aria-label="Cutaway illustration of a two-storey house interior" style="left:264px;top:3417px;width:390px;height:280px;clip-path:polygon(30% 0,100% 8%,100% 100%,0 100%,0 45%);background:linear-gradient(160deg,#555 0%,#2e2e2e 35%,#e9e6e0 40%,#c9c2b6 100%)"></div>

<form class="quote-card">
  <h3><span>GET</span> FREE QUOTE</h3>
  <p>If you have an any Question for<br>contact us Today !</p>
  <div class="field focus" style="top:166px">Name *</div>
  <div class="field" style="top:222px">Email *</div>
  <div class="field" style="top:277px">Phone *</div>
  <div class="field" style="top:333px;height:82px">Message *</div>
  <div class="btn" style="left:116px;top:430px;width:146px;height:53px;font-size:17px">Submit</div>
</form>

<div class="brand" style="left:78px;top:3738px;font-size:22px"><span class="mark"></span>BRINDLEWORK</div>
<svg class="abs" style="left:78px;top:3818px" width="18" height="26" viewBox="0 0 18 26"><path d="M9 1C4.6 1 1 4.6 1 9c0 6 8 16 8 16s8-10 8-16c0-4.4-3.6-8-8-8z" fill="var(--orange)"/><circle cx="9" cy="9" r="3" fill="var(--dark)"/></svg>
<div class="f-item" style="left:113px;top:3815px;width:220px">101 Lorem ipsum simple text<br>print type industry</div>
<svg class="abs" style="left:78px;top:3880px" width="20" height="15" viewBox="0 0 20 15"><rect width="20" height="15" rx="2" fill="var(--orange)"/><path d="M1 2l9 7 9-7" stroke="var(--dark)" stroke-width="1.6" fill="none"/></svg>
<div class="f-item" style="left:113px;top:3876px">info@brindlework.com</div>

<div class="footer-col"><h4 style="left:380px"><span>Contact</span> Us</h4></div>
<svg class="abs" style="left:380px;top:3814px" width="18" height="18" viewBox="0 0 18 18"><path d="M3 1l4 4-2 3c1 2 3 4 5 5l3-2 4 4-3 3C7 18 0 11 0 4z" fill="var(--orange)"/></svg>
<div class="f-item" style="left:412px;top:3810px">123 456 7890</div>
<div class="f-item" style="left:412px;top:3842px">123 456 7890</div>

<div class="footer-col"><h4 style="left:592px"><span>Site</span>map</h4></div>
<span class="bullet" style="left:594px;top:3819px"></span><div class="f-item" style="left:614px;top:3810px">Home</div>
<span class="bullet" style="left:594px;top:3852px"></span><div class="f-item" style="left:614px;top:3843px">About</div>
<span class="bullet" style="left:594px;top:3885px"></span><div class="f-item" style="left:614px;top:3876px">Services</div>
<span class="bullet" style="left:740px;top:3819px"></span><div class="f-item" style="left:759px;top:3810px">Testimonials</div>
<span class="bullet" style="left:740px;top:3852px"></span><div class="f-item" style="left:759px;top:3843px">Gallery</div>
<span class="bullet" style="left:740px;top:3885px"></span><div class="f-item" style="left:759px;top:3876px">Contact</div>

<div class="footer-col"><h4 style="left:919px"><span>Folow</span> Us</h4></div>
<div class="social" style="left:922px"></div>
<div class="social" style="left:980px"></div>
<div class="social" style="left:1037px"></div>

<footer class="copyright">© BRINDLEWORK – 2020 All rights reserved.</footer>

</body>
</html>
```